This book will apply the 12 Steps to gaming addiction, also known as video game addiction. The primary purpose of the book is to provide an effective solution for this new type of addiction. The solution is based on the rich and successful concepts of traditional twelve-step programs like RQ.

The title on the cover will be "Nine Doors Out of the Endless Level" and "by Peter Halvorn". A subtitle can be used if it works in your design of "A Practical Path Back from Compulsive Screen Play". Cover will be for a 6" x 9" book approximately 110 pages in length.

Some back cover text including some review quotes and an author bio are in the attached Word doc. There is also an author photo attached for for the back cover.

Requirements
Must have
• For the cover design it could be stylized, or an image, a partial image, or whatever. I am open to suggestions. Think about what would be noticed by a person searching for help with moderating their video game use, or by the parents or loved ones of problem gamers. Something contemporary and eye catching.

```html
<!DOCTYPE html>
<html lang="en">
<head>
<meta charset="utf-8">
<title>Nine Doors Out of the Endless Level — Book Cover</title>
<link rel="stylesheet" href="https://fonts.googleapis.com/css2?family=Saira+Condensed:wght@400;500;600&family=Poppins:wght@400;600;700&display=swap">
<style>
  :root {
    --page-bg: #e9e6e2;
    --cover-bg: #050508;
    --orange: #ff8a4c;
    --salmon: #f6a38a;
    --pink: #f2607a;
    --violet: #a98be6;
    --blue: #5e8fe0;
    --white: #ffffff;
    --gold: #f3c230;
    --rule: #7f93c9;
  }
  * { margin: 0; padding: 0; box-sizing: border-box; }
  html, body { width: 1200px; height: 1000px; overflow: hidden; }
  body { background: var(--page-bg); position: relative; }

  .cover {
    position: absolute; left: 280px; top: 20px;
    width: 640px; height: 960px;
    background: var(--cover-bg);
    overflow: hidden;
    font-family: "Saira Condensed", "Arial Narrow", sans-serif;
    color: var(--white);
  }

  .cover-art {
    position: absolute; left: 0; top: 300px; width: 640px; height: 660px;
    background:
      radial-gradient(ellipse 42% 30% at 50% 30%, rgba(90,110,230,.85), transparent 70%),
      radial-gradient(ellipse 55% 45% at 48% 45%, rgba(220,70,140,.75), transparent 75%),
      radial-gradient(ellipse 30% 14% at 45% 78%, rgba(230,60,80,.7), transparent 75%),
      radial-gradient(ellipse 20% 60% at 5% 70%, rgba(24,167,122,.35), transparent 80%),
      linear-gradient(180deg, var(--cover-bg) 0%, #2a0d2a 30%, #3a1240 60%, #0b0b1e 100%);
  }

  .title { position: absolute; inset: 0; font-weight: 500; }
  .title-line {
    position: absolute; display: block; line-height: .8;
    text-transform: uppercase; white-space: nowrap;
  }

  .t-nine {
    left: 62px; top: 104px; font-size: 120px; letter-spacing: -1px;
    transform: scaleY(1.75); transform-origin: left top;
    background: linear-gradient(180deg, var(--orange), var(--salmon));
    -webkit-background-clip: text; background-clip: text; color: transparent;
  }
  .t-doors {
    left: 64px; top: 338px; font-size: 80px;
    background: linear-gradient(180deg, var(--salmon), #ffd0c0);
    -webkit-background-clip: text; background-clip: text; color: transparent;
  }
  .t-outof { left: 338px; top: 98px; font-size: 40px; color: var(--white); }
  .t-endless {
    left: 308px; top: 152px; font-size: 88px;
    background: linear-gradient(90deg, var(--violet), var(--blue));
    -webkit-background-clip: text; background-clip: text; color: transparent;
  }
  .t-level {
    left: 308px; top: 262px; font-size: 130px;
    background: linear-gradient(90deg, var(--orange), var(--pink));
    -webkit-background-clip: text; background-clip: text; color: transparent;
  }

  .title-rules { position: absolute; left: 0; top: 0; }

  .endorsement {
    position: absolute; left: 50px; right: 50px; top: 462px;
    text-align: center; font-family: "Poppins", Arial, sans-serif;
  }
  .endorsement-quote { font-size: 15.5px; font-weight: 700; line-height: 1.35; color: var(--white); }
  .endorsement-source { margin-top: 3px; font-size: 14px; font-weight: 400; color: var(--white); }
  .endorsement-name { color: var(--gold); font-weight: 700; }

  .author {
    position: absolute; left: 0; right: 0; bottom: 48px;
    text-align: center; font-size: 74px; font-weight: 400;
    letter-spacing: 9px; line-height: 1; text-transform: uppercase;
    white-space: nowrap;
  }
</style>
</head>
<body>
  <main class="cover">
    <div class="cover-art" role="img" aria-label="Photograph of a person holding a glowing game controller in open hands, lit in magenta and blue over dark digital code"></div>

    <h1 class="title">
      <span class="title-line t-nine">Nine</span>
      <span class="title-line t-doors">Doors</span>
      <span class="title-line t-outof">Out of the</span>
      <span class="title-line t-endless">Endless</span>
      <span class="title-line t-level">Level</span>
    </h1>

    <svg class="title-rules" width="640" height="460" viewBox="0 0 640 460" aria-hidden="true">
      <g fill="none" stroke="var(--rule)" stroke-width="2">
        <polyline points="62,70 290,70 290,415 300,415"/>
        <line x1="290" y1="112" x2="312" y2="112"/>
      </g>
      <g fill="var(--rule)">
        <circle cx="320" cy="112" r="8"/>
        <circle cx="300" cy="415" r="8"/>
      </g>
    </svg>

    <section class="endorsement">
      <p class="endorsement-quote">“A must-read for anyone who is addicted to or thinks they may have a problem with digital gaming...”</p>
      <p class="endorsement-source"><span class="endorsement-name">DALE MARROW</span> | Noted Interventionist and Keynote Speaker</p>
    </section>

    <p class="author">Peter Halvorn</p>
  </main>
</body>
</html>
```